Stationery Set for Velmora Company

I need to create full stationery design for my company; Business Cards, Envelops, Letter Heads, Calendar.
In the letter head and Envelops... only contact information and website links.
Our company is a Service Management company with different domains of innovative services including Technology Service Management, Education Services, Outsourcing Management, Events Management.
I need a modern and innovative design specially for the business card. I some transparent designs and I like it, but don't limit your innovation to what I mentioned. Sky is limit for your innovation.

Target Market(s)

Middle East & Africa

Industry/Entity Type

Business Management

Colors
34a7d8
0355a3
85acd3
86cae7
cee9f5
cfdeed
e4daeb
f3f1f8
ecf7fb

Requirements
Must have
• Name, Title, Email, Mobile
Nice to have
• We have multiple locations in USA, KSA, EGY, so I need ideas about how to include all contact details maybe QR / Barcode or something else.
• Please see our locations and contact information: www.brightvelmora.example
Should not have
• Too much text

```html
<!DOCTYPE html>
<html lang="en">
<head>
<meta charset="utf-8">
<title>Velmora Company – Business Card</title>
<link rel="stylesheet" href="https://fonts.googleapis.com/css2?family=Fira+Sans:wght@400;500;600&display=swap">
<style>
  :root {
    --page: #9b9b9b;
    --card: #f1f1f3;
    --brand-blue: #3a62a8;
    --ink: #1f1f24;
    --rule: #3a62a8;
    --band-grey: #b3b1b6;
    --pattern-top: #eceef4;
    --pattern-bottom: #dde3ef;
  }
  * { box-sizing: border-box; margin: 0; padding: 0; }
  html, body { width: 1105px; height: 1200px; overflow: hidden; }
  body {
    background: var(--page);
    font-family: "Fira Sans", Arial, sans-serif;
    color: var(--ink);
    position: relative;
  }
  .card {
    position: absolute;
    left: 182px;
    width: 748px;
    height: 427px;
    background: var(--card);
    overflow: hidden;
    box-shadow: 0 14px 22px rgba(0,0,0,0.28);
  }
  .card--front { top: 119px; }
  .card--back { top: 637px; }

  .wordmark {
    position: absolute;
    display: flex;
    align-items: center;
    gap: 10px;
    color: var(--brand-blue);
    font-weight: 600;
    font-size: 50px;
    line-height: 1;
    letter-spacing: 0.5px;
  }
  .wordmark__dot {
    width: 18px; height: 18px;
    border-radius: 50%;
    background: var(--brand-blue);
  }
  .card--front .wordmark { right: 28px; top: 70px; }
  .card--back .wordmark { left: 50%; top: 112px; transform: translateX(-50%); }

  .holder { position: absolute; left: 37px; top: 177px; }
  .holder__name { color: var(--brand-blue); font-size: 25px; font-weight: 500; line-height: 1.1; }
  .holder__title { font-size: 18px; line-height: 1.4; }

  .divider {
    position: absolute; left: 37px; top: 240px;
    width: 670px; height: 2px; background: var(--rule);
  }

  .office { position: absolute; top: 250px; font-size: 16.5px; line-height: 22.5px; font-style: normal; }
  .office--ksa { left: 37px; }
  .office--usa { left: 292px; top: 272px; }
  .office__label { color: var(--brand-blue); text-transform: uppercase; }
  .office__phone-label { color: var(--brand-blue); }

  .contacts {
    position: absolute; left: 496px; top: 308px;
    list-style: none; font-size: 15.5px; white-space: nowrap;
  }
  .contacts li { display: flex; align-items: center; gap: 9px; height: 28.5px; }
  .contacts svg { width: 18px; height: 18px; flex: none; }

  .edge-band { position: absolute; left: 0; bottom: 0; width: 100%; height: 11px; display: flex; }
  .edge-band__blue { width: 563px; background: var(--brand-blue); }
  .edge-band__grey { flex: 1; background: var(--band-grey); }

  .bulb-pattern {
    position: absolute; left: 0; bottom: 0; width: 100%; height: 180px;
    background: linear-gradient(180deg, var(--pattern-top), var(--pattern-bottom));
  }
</style>
</head>
<body>

<section class="card card--front" aria-label="Business card front">
  <div class="wordmark"><span class="wordmark__dot"></span>Velmora</div>

  <div class="holder">
    <p class="holder__name">Karim Nasser</p>
    <p class="holder__title">CEO/Founder</p>
  </div>

  <div class="divider"></div>

  <address class="office office--ksa">
    <p class="office__label">Saudi Arabia:</p>
    <p>Riyadh, Al Nakheel,</p>
    <p>Rawdah Al Fursan St.</p>
    <p>Sidra Towers</p>
    <p>Block 4C 3rd Floor C12, C14</p>
    <p><span class="office__phone-label">Phone :</span> +966 92000 11 87</p>
  </address>

  <address class="office office--usa">
    <p class="office__label">USA:</p>
    <p>418 Harbor Crest Drive</p>
    <p>4th Floor Lakeview City</p>
    <p>CA 90017 US</p>
    <p><span class="office__phone-label">Phone:</span>+1.5550148821</p>
  </address>

  <ul class="contacts">
    <li>
      <svg viewBox="0 0 18 18" aria-hidden="true"><rect x="4.5" y="1" width="9" height="16" rx="1.5" fill="none" stroke="#3a62a8" stroke-width="1.6"/><rect x="6.3" y="3" width="5.4" height="9.5" fill="#3a62a8"/><circle cx="9" cy="14.6" r="0.9" fill="#3a62a8"/></svg>
      <span>+1.5550148821</span>
    </li>
    <li>
      <svg viewBox="0 0 18 18" aria-hidden="true"><rect x="1.5" y="4" width="15" height="10" fill="#3a62a8"/><path d="M1.5 4 L9 10 L16.5 4" fill="none" stroke="#f1f1f3" stroke-width="1.3"/></svg>
      <span>info@brightvelmora.example</span>
    </li>
    <li>
      <svg viewBox="0 0 18 18" aria-hidden="true"><circle cx="9" cy="9" r="7.5" fill="#3a62a8"/><path d="M5 6 Q8 5 8 8 Q6 10 8 13 M11 4.5 Q10 8 13 9" fill="none" stroke="#f1f1f3" stroke-width="1.3"/></svg>
      <span>www.brightvelmora.example</span>
    </li>
  </ul>

  <div class="edge-band"><span class="edge-band__blue"></span><span class="edge-band__grey"></span></div>
</section>

<section class="card card--back" aria-label="Business card back">
  <div class="wordmark"><span class="wordmark__dot"></span>Velmora</div>
  <div class="bulb-pattern" role="img" aria-label="Faint repeating pattern of light bulb outlines across the lower part of the card"></div>
</section>

</body>
</html>
```